ORV Web Design Project

I'm looking for a small, friendly,functional, information based website. If you go through the attachments, you would know the nature of the business.
Updates

Hi,

I have uploaded a picture of the CEO, Mr. Delvan Kroth PLMAT member. Please feel free to use it whereever appropriate.

Thanks!

Hello, I have uploaded some references. I like the colours used on the bar and would w

Example of a we page . I like this layout for the inside pages.

I am changing the tabs on my website to:

Home
About us
Services
Contact us

The services tab will have three sub pages:

Immigration
Education
AccommodationAccommodation

Target Market(s)

Young international students willing to come to Canada to study, young international students willing to immigrate to Canada, parents of the students

Industry/Entity Type

Business

Requirements
Must have
• ORV HOME
ABOUT US
CONTACT
SERVICES
TAG LINE

The website should look n feel trendy, smart, current, factual, trustworthy etc....
Nice to have
• I am looking for a bold, attractive, eye catchy home page with less text! Something that makes a statement....
Should not have
• No Clip art, flash animation, no bells n whistles please

```html
<!DOCTYPE html>
<html lang="en">
<head>
<meta charset="utf-8">
<title>ORV — Taking You Onwards</title>
<link rel="stylesheet" href="https://fonts.googleapis.com/css2?family=Open+Sans:ital,wght@0,300;0,400;0,600;0,700;0,800;1,400&display=swap">
<style>
:root{
  --red:#c8101a;
  --red-dark:#7a0309;
  --red-mid:#a80812;
  --white:#ffffff;
  --panel-grey:#eeeeee;
  --text:#3a3a3a;
  --heading:#1e1e1e;
  --nav:#777777;
  --orange:#e89a1c;
  --rule:#d0d0d0;
  --slate:#3c4a5c;
}
*{box-sizing:border-box;margin:0;padding:0}
html,body{width:789px;height:1200px;overflow:hidden}
body{
  position:relative;
  font-family:"Open Sans",Arial,sans-serif;
  color:var(--text);
  background:radial-gradient(ellipse at 50% 40%,var(--red) 0%,var(--red-mid) 55%,var(--red-dark) 100%);
}
.page{position:absolute;left:64px;top:32px;width:663px;height:1112px;background:var(--white);border-radius:3px;overflow:hidden}
.abs{position:absolute}

/* header */
.brand{left:29px;top:22px;width:130px}
.brand-name{display:flex;align-items:center;gap:8px;font-weight:800;font-size:38px;line-height:1;color:var(--red);letter-spacing:1px}
.brand-dot{width:14px;height:14px;border-radius:50%;background:var(--red)}
.brand-sub{margin-top:6px;font-size:10px;color:#555;border-top:1px solid #999;padding-top:3px;white-space:nowrap}
.tagline{right:24px;top:44px;font-weight:800;font-size:25px;letter-spacing:1.5px;color:#111}
.tagline em{font-style:normal;color:var(--red)}
.nav{right:24px;top:80px;display:flex;gap:20px;font-size:12px;color:var(--nav);list-style:none}
.nav .active{color:var(--orange)}

/* sections */
.section{position:absolute;left:0;width:663px}
.sec-immigration{top:131px;height:248px;background:var(--panel-grey)}
.sec-education{top:379px;height:322px;background:var(--white)}
.sec-accommodation{top:701px;height:330px;background:var(--panel-grey)}
.sec-footer{top:1031px;height:81px;background:var(--white)}

h2{font-size:14px;font-weight:600;color:var(--heading);letter-spacing:.3px}
p{font-size:9.1px;line-height:13.4px;text-align:justify}
a,.link{color:var(--red);text-decoration:none}
p+p{margin-top:13px}

.imm-title{left:21px;top:17px}
.imm-text{left:21px;top:42px;width:392px}
.imm-visual{left:429px;top:10px;width:134px;height:160px;border-radius:6px;background:linear-gradient(150deg,#26334f,#111a2d 70%,#3a4660)}
.imm-badge{left:473px;top:181px}

.edu-photo{left:24px;top:26px;width:208px;height:190px;background:radial-gradient(circle at 45% 40%,#2b2b2b 0%,#3a3a3a 35%,#f5f0e0 60%,#ffffff 80%)}
.edu-title{left:253px;top:24px}
.edu-intro{left:253px;top:48px;width:390px}
.col{position:absolute;top:165px;width:164px}
.col-inst{left:253px}
.col-stud{left:451px;width:192px}
.col h3{font-size:9px;font-weight:700;color:var(--heading);margin-bottom:2px}
.col p{text-align:justify}
.quote{margin-top:24px;font-style:italic;color:#555}
.sig{margin-top:24px;font-size:9px;font-weight:700;color:var(--red);line-height:12.5px}
.col-divider{left:437px;top:165px;width:1px;height:150px;background:var(--rule)}

.acc-title{left:21px;top:24px}
.acc-text{left:21px;top:48px;width:392px}
.acc-map{left:430px;top:24px;width:218px;height:158px;transform:rotate(2deg);border:5px solid var(--white);box-shadow:0 2px 5px rgba(0,0,0,.35);background:linear-gradient(120deg,#e9e6df 0%,#e3e0d8 55%,#9fc4e6 70%,#a9cdee 100%)}
.acc-photo{left:440px;top:163px;width:200px;height:146px;transform:rotate(-1.5deg);border:5px solid var(--white);box-shadow:0 2px 6px rgba(0,0,0,.4);background:linear-gradient(180deg,#cfe0d6 0%,#7fa65a 45%,#5f8d3c 70%,#8cb25c 100%)}

.foot-brand{left:129px;top:20px;display:flex;align-items:center;gap:6px;font-weight:800;font-size:24px;color:var(--red)}
.foot-brand .brand-dot{width:10px;height:10px}
.foot-claim{left:219px;top:18px}
.foot-claim .line1{font-size:20px;font-weight:400;letter-spacing:.8px;color:var(--slate);line-height:1.1}
.foot-claim .line1 span{color:var(--red)}
.foot-claim .line2{font-size:10.5px;color:var(--slate);margin-top:3px}

.copyright{position:absolute;left:0;top:1157px;width:789px;text-align:center;font-size:8.5px;color:var(--white)}
</style>
</head>
<body>
<div class="page">
  <header>
    <div class="abs brand">
      <div class="brand-name"><span>ORV</span><span class="brand-dot"></span></div>
      <div class="brand-sub">Onward Route Ventures</div>
    </div>
    <div class="abs tagline">Taking You <em>Onwards</em></div>
    <ul class="abs nav">
      <li>Home</li><li>About Us</li><li class="active">Services</li><li>Contact</li><li>ORV Mission</li>
    </ul>
  </header>

  <section class="section sec-immigration">
    <h2 class="abs imm-title">IMMIGRATION</h2>
    <div class="abs imm-text">
      <p>Canada has been consistently rated by the United Nations as one of the top countries in the world to live, work, and perform business in, owing to its large land size housing a relatively small population. Interestingly, it has one of the highest levels of immigration per capita in the world. ORV believes that immigration has contributed significantly to Canada's social, economic, and demographic growth, a trend that we continue to see today.</p>
      <p>Delvan Kroth has been an PLMAT (Professional League of Migration Advisors &amp; Trainers) member since 2011. PLMAT is the national regulatory authority designated by the Government of Canada to safeguard consumers who seek and retain the services of Canadian immigration consultants. Mr Kroth is authorized to provide the services of a Regulated Canadian Immigration Consultant.</p>
      <p>We are happy to answer your questions by email at <span class="link">immigration@orvgroup.example</span></p>
      <p>&nbsp;For more details and updates, please visit <span class="link">www.canadaportal.example</span>.</p>
    </div>
    <div class="abs imm-visual" role="img" aria-label="Photo of two Canadian passports"></div>
    <svg class="abs imm-badge" width="130" height="56" viewBox="0 0 130 56" role="img" aria-label="Regulatory council membership badge">
      <circle cx="27" cy="28" r="24" fill="#4a8cc9"/>
      <rect x="60" y="14" width="64" height="28" rx="4" fill="#4a8cc9"/>
    </svg>
  </section>

  <section class="section sec-education">
    <div class="abs edu-photo" role="img" aria-label="Photo of a graduation cap with a diploma tied in red ribbon"></div>
    <h2 class="abs edu-title">EDUCATION</h2>
    <p class="abs edu-intro">Canada has one of the finest education systems in the world. Every year thousands of students from all over the world pursue their educational goals in Canada. International Education has been recognized an important tool in building ties between nations. ORV prides itself on taking a vibrant approach to International Education, and we look forward to working with you to meet your individual needs.</p>
    <div class="col col-inst">
      <h3>INSTITUTIONS</h3>
      <p>If you are a Canadian institute, and would like to grow your recruitment numbers or develop business from India, please contact <span class="link">india@orvgroup.example</span>.</p>
      <p class="quote">" ORV help us to reach global opportunities and gain more revenue. We surely will continue our agreements with ORV for years to come. "</p>
      <div class="sig">Marcus Peller<br>CEO NORTHWIRE TELECOM</div>
    </div>
    <div class="abs col-divider"></div>
    <div class="col col-stud">
      <h3>STUDENTS</h3>
      <p>If you are a student aspiring to study in Canada, please contact us at <span class="link">student@orvgroup.example</span></p>
      <p class="quote">" I"m on my third year at Canada to have more international education. Thanks to ORV, everything here is easy and smooth. Can't wait for my graduation. "</p>
      <div class="sig">Ravin Dhall<br>STUDENT at LAKESHORE UNIVERSITY</div>
    </div>
  </section>

  <section class="section sec-accommodation">
    <h2 class="abs acc-title">STUDENT ACCOMMODATION SERVICES</h2>
    <div class="abs acc-text">
      <p>We have assisted many international students find a home away from home in Canada. International students trust us because we care. With our comprehensive application and matching systems, we are able to secure accommodation that is appropriate to your needs. When you deal with us, you can expect the kind of personal attention you would receive from your own family and friends. At ORV, we understand the importance of a living environment that supports both your educational priorities and lifestyle choices. We believe that finding the right accommodation is closely tied to academic success.</p>
      <p>Securing comfortable, affordable accommodation in a convenient location with the right mix of people can take time hence ORV recommends you get in touch with us at the earliest possible opportunity.</p>
      <p>The fast-growing city of Barrie, Ontario, is located only an hour's drive away from lively Toronto. Barrie is a charming and vibrant community that offers a laid-back lifestyle for people who prefer a slower pace with the convenience of a bustling multicultural city only a short distance away. Surrounded by picturesque scenic wilderness, the city offers something for everyone – numerous winter recreation amenities, ample parkland, a breathtaking waterfront, a historic downtown area with terrific shopping, entertainment and dining options. In recent years, Barrie has transformed itself from a quaint vacation destination to a year-round thriving economy.</p>
    </div>
    <div class="abs acc-map" role="img" aria-label="Street map of Barrie with a location pin near the waterfront"></div>
    <div class="abs acc-photo" role="img" aria-label="Photo of a green park with willow trees and a park sign"></div>
  </section>

  <footer class="section sec-footer">
    <div class="abs foot-brand"><span>ORV</span><span class="brand-dot"></span></div>
    <div class="abs foot-claim">
      <div class="line1">DARE TO DREAM <span>CANADIAN</span></div>
      <div class="line2">Your best partner for immigration &amp; education solution in Canada.</div>
    </div>
  </footer>
</div>
<div class="copyright">Copyright © 2013 OnwardRouteVentures. All Rights Reserved.</div>
</body>
</html>
```